Garlic Farm for Farm Sales/Restaurant sales

Need a professional, but appealing to agriculture world. We are selling 27 kinds of Organic Garlic from a farm in Simla,CO. I have uploaded logo and business information-we are going to need a template, because I will need to use it for four separate people.
-We are trying to appeal to Farm to table restaurants
-As well as growers/farmers

Target Market(s)

Agriculture Sales/Restaurants-Organic

Industry/Entity Type

Agriculture

Contact Information for Business Card

Want it to look more unique then your average kelto stock card- I want it to look amazing

Font styles to use
Sans Serif

Colors
0455a3
ec1f27
fbed22
ffffff

Requirements
Must have
• Just be creative
Nice to have
• Colorful
Should not have
• plain

```html
<!DOCTYPE html>
<html lang="en">
<head>
<meta charset="utf-8">
<title>Prairie Clove Farm – Business Card</title>
<link href="https://fonts.googleapis.com/css2?family=Source+Sans+3:wght@400;600;700&display=swap" rel="stylesheet">
<style>
  :root {
    --stage: #5c5c5c;
    --card-white: #ffffff;
    --brand-red: #c20e2f;
    --brand-navy: #0c2d63;
    --text-dark: #3a3a3a;
    --pattern-red: #c5132f;
    --pattern-red-soft: #cf2a3e;
  }
  * { margin: 0; padding: 0; box-sizing: border-box; }
  html, body {
    width: 1200px; height: 900px; overflow: hidden;
    background: var(--stage);
    font-family: "Source Sans 3", "Myriad Pro", sans-serif;
  }
  .canvas { position: relative; width: 1200px; height: 900px; }

  .card {
    position: absolute; top: 306px;
    width: 438px; height: 271px;
    border-radius: 12px; overflow: hidden;
    box-shadow: 0 2px 6px rgba(0,0,0,.25);
  }
  .card--front { left: 150px; background: var(--card-white); }
  .card--back { left: 610px; background: var(--pattern-red); }

  .brand-name {
    font-weight: 700; color: var(--brand-navy);
    white-space: nowrap; text-align: center; line-height: 1;
  }

  /* front */
  .card--front .brand-name {
    position: absolute; left: 8px; width: 220px; top: 122px;
    font-size: 25px;
  }

  .contact-block { position: absolute; left: 248px; top: 48px; color: var(--text-dark); }
  .person-name { font-size: 20px; font-weight: 600; color: var(--brand-red); line-height: 1.1; }
  .person-role { font-size: 13px; margin-top: 5px; }
  .address { font-size: 12.5px; line-height: 16px; margin-top: 17px; }
  .contact-list { list-style: none; margin-top: 14px; font-size: 12.5px; line-height: 16px; }
  .contact-list li { display: flex; align-items: center; gap: 8px; }
  .contact-list svg { width: 10px; height: 10px; fill: var(--brand-red); flex: none; }

  .footer-band { position: absolute; left: 0; bottom: 0; width: 438px; height: 19px; }

  /* back */
  .clove-pattern {
    position: absolute; inset: 0;
    background: radial-gradient(circle at 50% 45%, var(--pattern-red-soft), var(--pattern-red) 70%);
  }
  .card--back .brand-name {
    position: absolute; left: 0; right: 0; top: 117px;
    font-size: 34px;
  }
</style>
</head>
<body>
<div class="canvas">

  <section class="card card--front">
    <div class="brand-name">Prairie Clove Farm</div>

    <div class="contact-block">
      <p class="person-name">Daniel Hart</p>
      <p class="person-role">Managing Director</p>
      <p class="address">1234, Address Goes Here<br>Country Name, 123456</p>
      <ul class="contact-list">
        <li><svg viewBox="0 0 10 10"><path d="M2 1l2 2-1 1.2c.6 1.2 1.6 2.2 2.8 2.8L7 6l2 2-1.3 1.3C4.5 9 1 5.5.7 2.3z"/></svg>123-456-7890</li>
        <li><svg viewBox="0 0 10 10"><rect x="1" y="3" width="8" height="6" rx="1"/><rect x="3" y="0.5" width="4" height="3" fill="none" stroke="#c20e2f"/></svg>123-456-7890</li>
        <li><svg viewBox="0 0 10 10"><path d="M0 2h10v6H0z"/><path d="M0 2l5 3.5L10 2" fill="none" stroke="#fff" stroke-width="1"/></svg>info@youremail.com</li>
        <li><svg viewBox="0 0 10 10"><path d="M4 6L6 4M3 5L1.5 6.5a1.4 1.4 0 002 2L5 7M7 5l1.5-1.5a1.4 1.4 0 00-2-2L5 3" fill="none" stroke="#c20e2f" stroke-width="1.3"/></svg>www.yourweb.com</li>
      </ul>
    </div>

    <svg class="footer-band" viewBox="0 0 438 19" preserveAspectRatio="none">
      <polygon points="0,0 222,0 236,19 0,19" fill="var(--brand-red)"/>
      <polygon points="232,0 438,0 438,19 246,19" fill="var(--brand-navy)"/>
    </svg>
  </section>

  <section class="card card--back">
    <div class="clove-pattern" role="img" aria-label="Repeating pattern of garlic bulbs in soft red tones"></div>
    <div class="brand-name">Prairie Clove Farm</div>
  </section>

</div>
</body>
</html>
```